Guided Study Tour - Klangtage Wendorf Two Sided Flyer

We need a two-sided flyer for a Guided Study Tour to Klangtage Wendorf. We want beautiful pictures of Germany and if possible some of the Halbig venues our participants will be visiting. I have also provided the content that needs to be included. Also, in the attached document I provided a link to the Klangtage event. Please read and watch the video to be inspired.
This flyer should be beautiful and engaging. It needs to grab your attention right away and really highlight the wonderful things that they will be doing and that are included in the tour. This is a once in a lifetime opportunity for people to experience. We are targeting Music Directors and Music professionals.
Both attached logos need to be present on the flyer.

```html
<!DOCTYPE html>
<html lang="en">
<head>
<meta charset="utf-8">
<title>Guided Study Tour – Klangtage Wendorf Flyer</title>
<link href="https://fonts.googleapis.com/css2?family=Montserrat:wght@600;700&family=Nunito+Sans:wght@400;600;700&family=Allura&display=swap" rel="stylesheet">
<style>
:root{
  --bg:#e9e6e1;
  --purple:#4e2a6e;
  --magenta:#9b1f55;
  --gold:#f2c34c;
  --white:#ffffff;
  --ink:#2a2a2a;
  --red:#c21d24;
  --deep-red:#8d1014;
  --orange:#f29a2e;
  --dark:#2a0c0c;
  --tick:#f0a02a;
}
*{margin:0;padding:0;box-sizing:border-box}
html,body{width:1200px;height:1200px;overflow:hidden;background:var(--bg)}
body{position:relative;font-family:"Nunito Sans",Arial,sans-serif}
.page{position:absolute;top:215px;width:544px;height:770px;background:var(--white);overflow:hidden;box-shadow:0 2px 6px rgba(0,0,0,.18)}
.page--front{left:28px}
.page--back{left:628px}

/* front */
.portrait{position:absolute;left:0;top:0;width:544px;height:710px;background:linear-gradient(120deg,#bdbdbd 0%,#7c7c7c 45%,#3c3c3c 100%)}
.side-panel{position:absolute;left:0;top:0;width:274px;height:710px;background:linear-gradient(180deg,rgba(78,42,110,.96) 0%,rgba(110,36,96,.93) 45%,rgba(160,30,80,.92) 100%)}
.tour-label{position:absolute;left:30px;top:40px;font:700 21px "Montserrat",sans-serif;color:var(--white)}
.event-title{position:absolute;left:22px;top:66px;font:400 88px/1 "Allura",cursive;color:var(--gold)}
.brand-top{position:absolute;right:22px;top:24px;display:flex;align-items:center;gap:6px;font:600 15px "Nunito Sans",sans-serif;color:var(--white)}
.brand-top .mark{width:22px;height:22px;border:2px solid var(--white)}
.section-title{position:absolute;left:27px;font:700 19px "Montserrat",sans-serif;color:var(--gold)}
.ticks{position:absolute;left:27px;list-style:none;color:var(--white);font-size:12.5px;line-height:16.4px;width:250px}
.ticks li{position:relative;padding-left:13px}
.ticks li::before{content:"";position:absolute;left:0;top:4px;width:6px;height:3.5px;border-left:2px solid var(--tick);border-bottom:2px solid var(--tick);transform:rotate(-45deg)}
.ticks .indent{display:block;padding-left:10px}
.performers{position:absolute;left:27px;top:396px;color:var(--white);font-size:9.5px;line-height:12.8px;width:240px}
.performers strong{font:700 10.5px "Montserrat",sans-serif;display:block;margin-bottom:1px}
.dates{position:absolute;right:26px;top:638px;text-align:right;color:var(--white);font-size:10.5px;line-height:12.8px}
.quote-strip{position:absolute;left:0;top:710px;width:544px;height:60px;background:#f3f3f5}
.quote{position:absolute;left:16px;top:10px;width:340px;text-align:center;font-size:8.6px;line-height:12.5px;color:var(--ink)}
.quote small{display:block;font-size:6.5px;line-height:10px}
.brand-bottom{position:absolute;right:28px;top:22px;display:flex;align-items:center;gap:5px;font:700 11px "Nunito Sans",sans-serif;color:var(--red)}
.brand-bottom .mark{width:10px;height:10px;background:var(--red)}

/* back */
.cityscape{position:absolute;left:0;top:0}
.intro{position:absolute;left:298px;top:95px;width:236px;font-size:10.2px;line-height:12.8px;color:var(--white)}
.plane{position:absolute;left:20px;top:412px}
.inclusions-title{position:absolute;left:22px;top:456px;font:700 16px "Montserrat",sans-serif;color:var(--red)}
.inclusions{position:absolute;list-style:none;font-size:10.2px;line-height:14.6px;color:var(--ink)}
.inclusions li{position:relative;padding-left:14px}
.inclusions li::before{content:"";position:absolute;left:1px;top:3px;width:6px;height:3.5px;border-left:2px solid var(--tick);border-bottom:2px solid var(--tick);transform:rotate(-45deg)}
.inclusions .indent{display:block;padding-left:14px}
.inclusions--a{left:24px;top:478px;width:260px}
.inclusions--b{left:295px;top:478px;width:240px}
.bio-band{position:absolute;left:0;top:636px;width:544px;height:134px;background:var(--red)}
.photo-slot{position:absolute;left:20px;top:10px;width:106px;height:108px;background:#f4f4f4;display:flex;align-items:center;justify-content:center;font-size:9px;color:var(--ink)}
.bio{position:absolute;left:136px;top:8px;width:392px;font-size:8.4px;line-height:11px;color:var(--white);text-align:justify}
.contact-bar{position:absolute;left:136px;top:98px;width:408px;height:20px;background:var(--dark);color:var(--white);font-size:9px;text-align:right;padding:4px 24px 0 0}
</style>
</head>
<body>

<section class="page page--front">
  <div class="portrait" role="img" aria-label="Black and white engraved portrait of the composer seated at a keyboard"></div>
  <div class="side-panel"></div>
  <div class="tour-label">Guided Study Tour</div>
  <div class="event-title">Klangtage</div>
  <div class="brand-top"><span class="mark"></span>Harlow Tours</div>

  <h2 class="section-title" style="top:234px">Klangtage Highlights:</h2>
  <ul class="ticks" style="top:263px">
    <li>More than 100 Concerts in 42 different <span class="indent">Halbig venues</span></li>
    <li>World Class Musicians &amp; Celebrated <span class="indent">Recording Artists</span></li>
    <li>Day trips to Weimer &amp; Dresden</li>
    <li>Bilingual pre-concert talks &amp; lectures with <span class="indent">Halbig Scholars</span></li>
  </ul>
  <div class="performers"><strong>Featured Performers:</strong>Jonas Sorel, Tomas Kerling, Vocalis,<br>Wendorf Hall Orchestra, Lumena,<br>&amp; the Wendorf Boys Choir</div>

  <h2 class="section-title" style="top:478px">Study Tour Highlights:</h2>
  <ul class="ticks" style="top:507px">
    <li>Access to dress rehearsals</li>
    <li>Meet the artist opportunities Post-concert <span class="indent">discussions led by Daniel Reeve</span></li>
    <li>Study sessions on Halbig’s B-Minor Mass, <span class="indent">Magnificat, St. John Passion,</span><span class="indent">St. Matthew Passion &amp; Weimar</span><span class="indent">Cantatashours</span></li>
    <li>Guidance in planning individual <span class="indent">concert itinerary</span></li>
    <li>Professional development or continuing <span class="indent">education credit</span></li>
  </ul>
  <div class="dates">June 12-16, 2019<br>Wendorf, Germany<br>Plus day trip to Dresden and full day<br>and overnight in Prague</div>

  <div class="quote-strip">
    <p class="quote">“This is where it all has begun...this is why our guests have tears in their eyes listening to the St. Matthew Passion or the B-Minor Mass”<small>~ Martin Adler, Musicologist, Festival Director</small></p>
    <div class="brand-bottom"><span class="mark"></span>Meridian Choral Tours</div>
  </div>
</section>

<section class="page page--back">
  <svg class="cityscape" width="544" height="470" viewBox="0 0 544 470">
    <defs>
      <linearGradient id="sky" x1="0" y1="0" x2="0" y2="1">
        <stop offset="0" stop-color="#3d4f7a"/>
        <stop offset=".18" stop-color="#e8a878"/>
        <stop offset=".32" stop-color="#4a5d86"/>
        <stop offset=".7" stop-color="#2b2f45"/>
        <stop offset="1" stop-color="#6a4a2a"/>
      </linearGradient>
    </defs>
    <path d="M0 360 C160 470 430 470 544 330 V420 C430 480 160 480 0 380 Z" fill="var(--deep-red)"/>
    <path d="M0 340 C160 455 430 460 544 330 V360 C430 470 160 470 0 362 Z" fill="var(--orange)"/>
    <path d="M0 0 H544 V330 C430 450 160 450 0 336 Z" fill="url(#sky)" role="img" aria-label="Night photograph of a twin-spired cathedral and an illuminated river bridge"/>
  </svg>
  <p class="intro">Daniel Reeve partnered with Meridian Choral Tours to bring you and experience of a Lifetime. With over 100 years of combined educational student travel expertise, Meridian Choral Tours, powered by Harlow Tours, brings unparalleled tour experiences for you and your students.</p>

  <svg class="plane" width="58" height="38" viewBox="0 0 58 38" aria-hidden="true">
    <path d="M2 24 L14 22 L34 8 L42 6 L36 16 L56 14 L50 20 L34 24 L24 36 L18 36 L22 26 L8 28 Z" fill="var(--red)"/>
    <path d="M2 24 L14 22 L22 26 L8 28 Z" fill="var(--purple)"/>
  </svg>
  <h2 class="inclusions-title">TRIP INCLUSIONS</h2>
  <ul class="inclusions inclusions--a">
    <li>Roundtrip Airfare from Houston</li>
    <li>13 Nights Accomodations, <span class="indent">3 Star Hotels with A/C</span></li>
    <li>Daily Breakfast</li>
    <li>Access to rehearsal sessions</li>
    <li>Pirvate Luxury Coach Transfer Services <span class="indent">for airport transfers and day tours to Berlin,</span><span class="indent">Weimar and Dresden &amp; Prague.</span></li>
    <li>Professional Local Guides for for City Tours in: <span class="indent">Berlin, Weimar, Dresden &amp; Prague</span></li>
  </ul>
  <ul class="inclusions inclusions--b">
    <li>Entrance Fees to: House of Lukas Brenner, <span class="indent">Franz Haller, Gerlach in Weimar, Lutheran</span><span class="indent">Frauenkirche &amp; Alte Meister Gallery in the</span><span class="indent">Zwiner Palace in Dresend, and Cathedral</span><span class="indent">and Golden Lane in Prague</span></li>
    <li>All Applicable Taxes and Gratuities <span class="indent">for Included Services, Guides, and Drivers</span></li>
    <li>$2 Million in Professional Liability Insurance</li>
    <li>24-hour Travel Support Staff</li>
  </ul>

  <div class="bio-band">
    <div class="photo-slot" role="img" aria-label="Portrait photo placeholder">Daniel’s photo</div>
    <p class="bio">Daniel Reeve is Director of Choral Studies at the Rio Verde State University and the conductor of the Valley Civic Chorale and the Valley Vocal Artists, a professional chamber choir. A native Texan, his degrees are from Hollis Pine University, Bayfield University and the Pacific Coast University. Recent engagements include conducting the Duvallé Requiem in Buffalo, NY, serving on the jury for the Aegean International Choral Festival in Preveza, Greece and the International Choir Championship ArsCanto in Tusnia, Bosnia and Herzogevina.</p>
    <div class="contact-bar">daniel.reeve@rverde.edu</div>
  </div>
</section>

</body>
</html>
```